New website for salon services and wedding hair and makeup

I am a professional hairstylist and makeup artist in Charleston, SC. I have my own company where I see clients for cut and color and I also go on site for weddings. I have a current website that I would like to update and change the style. I would like to add a contact form, map, additional pages and be mobile friendly. It is important to me that it have a site map and can show up in searches. I will need to add photos to the site every so often and would like to continue to work with the designer. I have a logo that I am happy with and have attached the file however if you think a new logo would help the look of the site I am open to it. My current website is www.brightcombstudio-example.com, I would like to change the style and layout so it looks up to date. Here are some links to sites that I like the look of but I don't want to limit your creativity. http://willowlanefolio-example.com/ http://www.runwaylensworks-example.com http://miraventhol-example.com/. I have attached a few files for mock up purposes, please let me know if you would like more content. Thank you!

Target Market(s)

Women, Brides

Industry/Entity Type

Hair And Beauty

Number of Pages Required

1 page

Font styles to use
Sans Serif
Script

Requirements
Must have
• Contact form, Mobile friendly, sitemap
Nice to have
• I really like the look for the sites I have included on the project description guide.
Should not have
• Nothing overly girly.

```html
<!DOCTYPE html>
<html lang="en">
<head>
<meta charset="utf-8">
<title>Brightcomb Studio — Hair &amp; Makeup</title>
<link rel="stylesheet" href="https://fonts.googleapis.com/css2?family=Great+Vibes&family=Montserrat:wght@400;600&family=Open+Sans:wght@400;600&display=swap">
<style>
:root{
  --navy:#1f3f5c;
  --navy-deep:#16314a;
  --sky:#9fd0e4;
  --ink:#2e3e4e;
  --muted:#6d7680;
  --accent:#d9773f;
  --paper:#ffffff;
  --mist:#f1f1f1;
  --stone:#5c5f5f;
  --rose:#c4575b;
}
*{box-sizing:border-box;margin:0;padding:0}
html,body{width:1200px;height:2980px;overflow:hidden}
body{background:var(--paper);font-family:"Open Sans",Arial,sans-serif;color:var(--ink);position:relative}

/* Hero */
.hero{position:absolute;left:0;top:0;width:1200px;height:652px;
  background:radial-gradient(ellipse at 58% 32%,#e9c9b3 0%,#b0826a 22%,#5a3d33 45%,#2d2a2d 70%,#1c2430 100%)}
.brand{position:absolute;left:30px;top:24px;display:flex;align-items:center;gap:12px}
.brand-mark{width:22px;height:22px;border-radius:50%;background:var(--sky)}
.brand-name{font-family:"Great Vibes",cursive;font-size:46px;color:var(--sky);line-height:1}
.main-nav{position:absolute;left:0;top:556px;width:1200px;height:96px;background:rgba(225,230,236,.82);
  display:flex;align-items:center;justify-content:center;gap:0}
.main-nav a{font-family:"Montserrat",Arial,sans-serif;font-size:17px;letter-spacing:3px;color:var(--navy);
  text-decoration:none;height:96px;display:flex;align-items:center;padding:0 42px}
.main-nav a.is-active{background:var(--navy);color:#fff}

/* About */
.about{position:absolute;left:40px;top:652px;width:1120px;height:410px;background:var(--paper);display:flex}
.about-photo{width:560px;height:392px;margin-top:8px;margin-left:40px;
  background:linear-gradient(135deg,#ece5df 0%,#b88a73 40%,#6a4436 70%,#ded6d0 100%)}
.about-copy{flex:1;text-align:center;padding:40px 60px 0}
.script-title{font-family:"Great Vibes",cursive;font-weight:400;color:var(--navy)}
.about-copy h2{font-size:56px;text-align:right;padding-right:20px}
.about-copy p{font-size:15px;line-height:1.75;color:var(--muted);margin:22px auto 0;width:340px}
.btn-outline{display:inline-block;margin-top:70px;border:1px solid var(--rose);color:var(--rose);
  font-size:14px;padding:14px 34px;text-decoration:none}

/* Gallery */
.gallery{position:absolute;left:0;top:1062px;width:1200px;height:680px;
  background:radial-gradient(circle at 50% 45%,#8b8d8b 0%,#6a6c6b 40%,#4d504f 100%)}
.gallery svg{position:absolute;left:0;top:0}

/* Services */
.services{position:absolute;left:40px;top:1742px;width:1120px;height:540px;background:var(--paper);display:flex}
.services-list{width:512px;padding:30px 0 0 40px}
.services-list h2{font-size:62px;margin-bottom:22px}
.svc{list-style:none;font-family:"Montserrat",Arial,sans-serif}
.svc>li{font-size:15px;letter-spacing:2px;text-transform:uppercase;color:var(--ink);margin-bottom:10px;font-weight:600}
.svc>li::before{content:"»";margin-right:10px;color:var(--ink)}
.svc>li.is-open{color:var(--accent)}
.svc ul{list-style:none;margin:10px 0 18px 36px}
.svc ul li{font-size:12px;letter-spacing:2px;color:var(--muted);font-weight:400;margin-bottom:9px}
.svc ul li.is-active{color:var(--accent);text-decoration:underline}
.services-photo{position:relative;width:568px;height:540px;
  background:linear-gradient(160deg,#7a2c2e 0%,#b8433f 35%,#e3c2ae 60%,#6a2b2a 100%)}
.slider-arrows{position:absolute;left:264px;bottom:36px}

/* Contact */
.contact{position:absolute;left:0;top:2282px;width:1200px;height:440px;
  background:linear-gradient(180deg,#243a52 0%,#3a5877 45%,#1f2e40 100%)}
.contact h2{color:#fff;text-align:center;font-size:58px;margin-top:44px}
.contact-form{position:absolute;left:392px;top:118px;width:408px}
.field{display:block;background:#fff;height:40px;font-size:12px;color:var(--muted);padding:12px 10px}
.field-row{display:flex;gap:8px}
.field-row .field{width:200px}
.field-area{height:108px;margin-top:12px}
.btn-submit{display:block;margin:20px auto 0;width:152px;height:40px;border:0;background:#fff;color:var(--navy);font-size:14px;font-family:"Open Sans",Arial,sans-serif}
.social{position:absolute;left:540px;top:366px;display:flex;gap:24px}
.social span{width:26px;height:26px;border-radius:50%;background:#fff;border:3px solid var(--sky)}

/* Map & footer */
.map{position:absolute;left:0;top:2722px;width:1200px;height:218px;
  background:linear-gradient(120deg,#e8e4d6 0%,#d7e2cf 30%,#f0ead5 55%,#cfdbe3 80%,#e6e2d2 100%)}
.site-footer{position:absolute;left:0;top:2940px;width:1200px;height:40px;background:var(--navy-deep);
  color:#c9d3dd;font-size:12px;text-align:center;line-height:40px}
</style>
</head>
<body>

<header class="hero" role="img" aria-label="Portrait photo of a woman with long curly brown hair and red lipstick">
  <div class="brand"><span class="brand-mark"></span><span class="brand-name">Brightcomb</span></div>
  <nav class="main-nav">
    <a href="#" class="is-active">HOME</a>
    <a href="#">ABOUT US</a>
    <a href="#">GALLERY</a>
    <a href="#">SERVICES</a>
    <a href="#">CONTACT</a>
  </nav>
</header>

<section class="about">
  <div class="about-photo" role="img" aria-label="Photo of a woman with long wavy auburn hair"></div>
  <div class="about-copy">
    <h2 class="script-title">About us</h2>
    <p>Brightcomb Studio specializes in providing gorgeous, long lasting hair and makeup. With over nine years of experience and training, we know how to make your day the very best. We take pride in client satisfaction.</p>
    <a href="#" class="btn-outline">Read More</a>
  </div>
</section>

<section class="gallery" role="img" aria-label="Gallery of circular hair styling photos around a central title">
  <svg width="1200" height="680" viewBox="0 0 1200 680">
    <g stroke="#fff" stroke-width="8">
      <circle cx="320" cy="278" r="132" fill="#a3683f"/>
      <circle cx="840" cy="238" r="100" fill="#8c7a6c"/>
      <circle cx="472" cy="450" r="112" fill="#d8b6a0"/>
      <circle cx="740" cy="450" r="130" fill="#c9b8ad"/>
      <circle cx="600" cy="258" r="168" fill="#274766"/>
    </g>
    <g stroke="#1f3f5c" stroke-width="14" stroke-linecap="square">
      <line x1="300" y1="278" x2="340" y2="278"/><line x1="320" y1="258" x2="320" y2="298"/>
    </g>
    <text x="600" y="270" text-anchor="middle" fill="#fff" font-family="Great Vibes, cursive" font-size="44">Show our Gallery</text>
  </svg>
</section>

<section class="services">
  <div class="services-list">
    <h2 class="script-title">Our Services</h2>
    <ul class="svc">
      <li>Bridal</li>
      <li>Hair Cut</li>
      <li class="is-open">Color
        <ul>
          <li>PARTIAL HIGHLIGHTS</li>
          <li class="is-active">FULL HIGHLIGHTS</li>
          <li>DOUBLE PROCESS</li>
          <li>OMBRE</li>
          <li>ROOTS WITH GLAZE</li>
          <li>ALL OVER COLOR</li>
        </ul>
      </li>
      <li>Styling and Treatments
        <ul>
          <li>BLOW OUT/WET STYLING</li>
          <li>EVENT UPSTYLE</li>
          <li>DEEP CONDITION</li>
          <li>KERATIN SMOOTHING TREATMENT</li>
        </ul>
      </li>
    </ul>
  </div>
  <div class="services-photo" role="img" aria-label="Photo of a woman with long red hair">
    <svg class="slider-arrows" width="40" height="24" viewBox="0 0 40 24">
      <polygon points="16,2 4,12 16,22" fill="#fff"/>
      <polygon points="24,2 36,12 24,22" fill="#fff"/>
    </svg>
  </div>
</section>

<section class="contact" role="img" aria-label="Evening photo of a cable-stayed bridge over water">
  <h2 class="script-title">Keep In Touch</h2>
  <form class="contact-form">
    <div class="field-row">
      <span class="field">name</span>
      <span class="field">email id</span>
    </div>
    <span class="field field-area">message</span>
    <button type="button" class="btn-submit">Submit</button>
  </form>
  <div class="social"><span></span><span></span><span></span></div>
</section>

<div class="map" role="img" aria-label="Street map showing the studio location"></div>

<footer class="site-footer">copyright 2013, All rights reserved by Brightcomb</footer>

</body>
</html>
```